Corvane Automotive Reconditioning Business Card

We need a professional business card that features our logo, a picture of the employee, and a brief list of our services.
I've attached a logo, and will attach photos at a later date.
The four services that need to be listed are Bumper repair and repainting, road rash repair, clear coat scratch repair, and automotive touch-up.
Target Market(s)
30 - 40 year male general managers of automobile dealerships. They are used to seeing every vendor gimmick under the sun. This brochure needs to impress with its simplicity and honesty.
Industry/Entity Type
Automotive
Look and feel

```html
<!DOCTYPE html>
<html lang="en">
<head>
<meta charset="utf-8">
<title>Corvane Automotive Reconditioning – Business Card</title>
<link rel="stylesheet" href="https://fonts.googleapis.com/css2?family=Open+Sans:wght@400;600;800&display=swap">
<style>
  :root {
    --bg: #d9d8d5;
    --charcoal: #333333;
    --charcoal-deep: #262626;
    --orange: #f15a22;
    --white: #ffffff;
    --ink: #2b2b2b;
    --muted: #444444;
    --photo-top: #b9c3d3;
    --photo-bottom: #3f5a86;
  }
  * { box-sizing: border-box; margin: 0; padding: 0; }
  html, body { width: 1200px; height: 900px; overflow: hidden; }
  body {
    background: var(--bg);
    font-family: "Open Sans", Arial, sans-serif;
    position: relative;
  }
  .card {
    position: absolute;
    left: 250px;
    width: 700px;
    height: 400px;
    overflow: hidden;
    box-shadow: 0 6px 18px rgba(0,0,0,0.18);
  }

  /* ----- Back side ----- */
  .card--back { top: 40px; background: var(--charcoal); }
  .card--back .wordmark {
    position: absolute; top: 110px; left: 0; right: 0;
    text-align: center; color: var(--white);
    font-weight: 800; line-height: 1;
  }
  .wordmark .wordmark-name { display: block; font-size: 66px; letter-spacing: 3px; }
  .wordmark .wordmark-sub { display: block; font-size: 17px; letter-spacing: 1.5px; margin-top: 8px; }
  .services-band {
    position: absolute; left: 0; right: 0; top: 306px; height: 34px;
    background: var(--white);
    border-top: 3px solid var(--orange);
    border-bottom: 3px solid var(--orange);
    display: flex; align-items: center; justify-content: center;
    white-space: nowrap;
    font-size: 12px; color: var(--ink); font-weight: 400;
  }
  .services-band span + span::before { content: "|"; margin: 0 6px; color: var(--ink); }

  /* ----- Front side ----- */
  .card--front { top: 460px; background: var(--white); }
  .employee-photo {
    position: absolute; left: 50px; top: 40px; width: 250px; height: 290px;
    background: linear-gradient(180deg, var(--photo-top), var(--photo-bottom));
  }
  .card--front .wordmark {
    position: absolute; top: 40px; right: 44px; text-align: left;
    color: var(--ink); font-weight: 800; line-height: 1;
  }
  .card--front .wordmark .wordmark-name { font-size: 54px; }
  .card--front .wordmark .wordmark-sub { font-size: 14px; }
  .contact {
    position: absolute; top: 150px; left: 380px;
    font-size: 15px; color: var(--muted); line-height: 21px;
    white-space: nowrap;
  }
  .contact .address { margin-bottom: 8px; }
  .contact li { list-style: none; display: flex; align-items: center; gap: 9px; }
  .contact svg { width: 13px; height: 13px; fill: var(--orange); flex: none; }
  .side-tab {
    position: absolute; right: 0; top: 246px; width: 100px; height: 40px;
  }
  .name-band {
    position: absolute; left: 0; right: 0; top: 330px; height: 44px;
    background: var(--charcoal-deep);
    border-top: 3px solid var(--orange);
    border-bottom: 3px solid var(--orange);
    display: flex; align-items: center; padding-left: 50px;
    color: var(--white); font-size: 24px; font-weight: 600; letter-spacing: 3px;
    white-space: nowrap;
  }
</style>
</head>
<body>

  <section class="card card--back" aria-label="Business card back">
    <div class="wordmark">
      <span class="wordmark-name">CORVANE</span>
      <span class="wordmark-sub">AUTOMOTIVE RECONDITIONING</span>
    </div>
    <div class="services-band">
      <span>Bumper repair and repainting</span>
      <span>Road rash repair</span>
      <span>Clear coat scratch repair</span>
      <span>Automotive touch-up</span>
    </div>
  </section>

  <section class="card card--front" aria-label="Business card front">
    <div class="employee-photo" role="img" aria-label="Portrait photo of the employee in a blue suit"></div>

    <div class="wordmark">
      <span class="wordmark-name">CORVANE</span>
      <span class="wordmark-sub">AUTOMOTIVE RECONDITIONING</span>
    </div>

    <div class="contact">
      <p class="address">4820 E. Larkspur Dr.<br>Mesa, AZ 85206</p>
      <ul>
        <li><svg viewBox="0 0 12 12"><path d="M2.5 1 L4.5 1 L5 3.5 L3.8 4.4 Q4.8 6.8 7.6 8.2 L8.5 7 L11 7.5 L11 9.5 Q11 11 9.5 11 Q1 10 1 2.5 Q1 1 2.5 1 Z"/></svg>555-214-0370</li>
        <li><svg viewBox="0 0 12 12"><path d="M3 0.5 H9 V11.5 H3 Z M4 2 V9 H8 V2 Z M5.5 9.7 H6.5 V10.6 H5.5 Z"/></svg>555-214-0380</li>
        <li><svg viewBox="0 0 12 12"><path d="M0.5 2.5 H11.5 V9.5 H0.5 Z M1.5 3.5 V8.5 H10.5 V3.5 L6 6.8 Z M2.2 3.5 L6 5.9 L9.8 3.5 Z"/></svg>info@corvaneauto.com</li>
        <li><svg viewBox="0 0 12 12"><path d="M6 0.5 A5.5 5.5 0 1 0 6.01 0.5 Z M6 1.5 A4.5 4.5 0 0 1 10.4 5.5 H1.6 A4.5 4.5 0 0 1 6 1.5 Z M1.6 6.5 H10.4 A4.5 4.5 0 0 1 1.6 6.5 Z"/></svg>www.corvaneauto.com</li>
      </ul>
    </div>

    <svg class="side-tab" viewBox="0 0 100 40" aria-hidden="true">
      <polygon points="16,0 100,0 100,40 0,40" fill="#333333"/>
      <polyline points="0,40 16,0 100,0" fill="none" stroke="#f15a22" stroke-width="3"/>
    </svg>

    <div class="name-band">DANIEL WHITFORD</div>
  </section>

</body>
</html>
```